Web Design For Marlow Pool Service

We are working with a company that wants a website for their pool service. Some sites to use for content/competitors and inspiration:
https://sacramento.brightwaterpoolco.example/builder/newbuild/repair/ppc
https://hollowbrookpoolcareplus.example/
https://lakemontpoolservice.example/
https://www.dravenspoolresurfacing.example/pool-renovation-ga/
Thank you for taking the time to consider designing a website for us. We are web developers based in Stockton, CA, USA. Most of our projects go through the same process. Understanding this process may help you win a project with us. We custom-code all of our websites in-house. We don’t have any requirements as to what tools you use for your design, but we prefer Figma files. For any design that we label as four-stars, we send it to the client for review. The client picks the final design they want us to use. Once we complete this process, we will continue to show additional clients all the four-star sites and purchase them later. Your designs will have multiple chances to sell. For better chances of success, we ask that you follow these guidelines.
IMAGES:
If you use any images or icons in the design, we ask that you have a link to the asset so we can purchase the image/icon. Most of the designs we submit do not have the customer’s images on them unless they have some great images. Be creative; show us the feeling you are trying to portray with your image choices. Use any royalty-free site you choose. We subscribe to Adobe and mainly use their images, but we can purchase images outside of Adobe. PLEASE NOTE: we will not submit designs to clients with watermarks on the images.
FONTS:
We ask that you identify the fonts used in the design. This can be done in a message if you want. We typically use Google Fonts and Adobe Fonts.
CONTENT:
We're always open to different content and ideas. We often submit designs with stock images so the client can see our vision. We typically take pictures after the website launch to use their images with our vision. Lorem Ipsum is fine for paragraphs, but we ask that you write the headers in correct English. We want to be able to show the vision and identify the sections of the website.
INSPIRATION:
We typically add a couple of links in the brief of websites we like to help you get started in your design.
REVISIONS:
We do not often ask for revisions of the designs unless we see something in the design that may not appeal to the client. If there are slight changes that we want to make, we do that in the development process.
FEEDBACK:
We rarely give feedback on designs during the design process. We are working on many website projects and do not have the time to provide feedback. We usually respond if your request is well thought out and asks specific questions, but a note asking “feedback, please” usually goes unanswered.
Number of Pages Required
1 page
Look and feel
Each slider illustrates characteristics of the customer's brand and the style your logo design should communicate.

```html
<!DOCTYPE html>
<html lang="en">
<head>
<meta charset="utf-8">
<title>Marlow Pool Service</title>
<link href="https://fonts.googleapis.com/css2?family=Cinzel:wght@400;600&family=Montserrat:wght@400;500;600&family=Poppins:wght@600;700&display=swap" rel="stylesheet">
<style>
:root{
  --aqua:#5fd4f7;
  --aqua-deep:#4cc4ee;
  --aqua-title:#55c9f0;
  --white:#ffffff;
  --ink:#2f3337;
  --muted:#5a5f64;
  --bar:#3a3f44;
}
*{margin:0;padding:0;box-sizing:border-box}
html,body{width:1200px;height:5348px;overflow:hidden}
body{position:relative;background:var(--white);font-family:"Montserrat",sans-serif;color:var(--ink)}
.abs{position:absolute}
.center{text-align:center}
.serif-title{font-family:"Cinzel",serif;font-weight:400;color:var(--aqua-title);letter-spacing:2px}
.pill{position:absolute;display:flex;align-items:center;justify-content:center;border-radius:40px;font-size:13px;font-weight:500;text-transform:uppercase;letter-spacing:.5px}
.pill-solid{background:var(--aqua);color:var(--white)}
.pill-line{border:2px solid var(--white);color:var(--white)}
.photo{position:absolute;overflow:hidden}

/* header */
.site-header{position:absolute;left:0;top:0;width:1200px;height:135px;background:var(--white)}
.brand{position:absolute;display:flex;align-items:center;gap:10px;font-family:"Cinzel",serif;font-weight:400;color:var(--aqua-deep);font-size:22px;letter-spacing:2px;line-height:1.1}
.brand-dot{width:26px;height:26px;border-radius:50%;background:var(--aqua);flex:none}
.nav a{position:absolute;top:68px;font-size:11.5px;font-weight:500;color:var(--ink);text-decoration:none;text-transform:uppercase}
.nav a.active{color:var(--aqua-deep)}

/* hero */
.hero{left:0;top:135px;width:1200px;height:662px;background:linear-gradient(160deg,#b48a5e 0%,#7fb7cc 28%,#2fa5e6 48%,#49c3f3 70%,#8a6a4c 100%)}
.hero-shade{position:absolute;inset:0;background:rgba(10,60,100,.18)}
.hero-kicker{top:168px;width:100%;font-family:"Cinzel",serif;font-size:34px;color:var(--white);letter-spacing:1px}
.hero-title{top:212px;width:100%;font-family:"Poppins",sans-serif;font-weight:700;font-size:78px;color:var(--white);text-shadow:0 4px 10px rgba(0,0,0,.45);letter-spacing:1px}
.hero-text{top:318px;width:100%;font-size:17px;color:var(--white);line-height:22px}

/* stats */
.stat{position:absolute;top:888px;width:243px;height:160px;background:var(--aqua);color:var(--white);text-align:center;box-shadow:0 3px 6px rgba(0,0,0,.12)}
.stat-icon{position:absolute;left:84px;top:-38px;width:76px;height:76px;border-radius:50%;background:var(--aqua);border:4px solid var(--white);display:flex;align-items:center;justify-content:center}
.stat-num{margin-top:50px;font-family:"Poppins",sans-serif;font-weight:700;font-size:40px;line-height:44px}
.stat-label{margin-top:6px;font-size:15px;line-height:19px;text-transform:uppercase}

/* intro video */
.video{left:73px;top:1200px;width:1052px;height:484px;background:linear-gradient(180deg,#3e5a3a 0%,#6a5a4a 25%,#3f86c4 45%,#62a7d8 100%)}
.play{position:absolute;left:466px;top:110px;width:96px;height:96px}
.intro-card{position:absolute;left:183px;top:1526px;width:834px;height:360px;background:var(--white)}
.intro-title{top:1592px;left:0;width:1200px;font-size:46px}
.intro-text{top:1682px;left:280px;width:640px;font-size:13px;line-height:23px;color:var(--ink)}

/* services */
.services{left:0;top:1987px;width:1200px;height:762px;background:var(--aqua)}
.services-title{top:88px;width:100%;font-size:56px;color:var(--white)}
.services-text{top:178px;left:70px;width:1060px;font-size:13px;line-height:23px;color:var(--white)}
.svc{position:absolute;top:278px;width:251px;height:266px;border-radius:14px;overflow:hidden;background:var(--white)}
.svc-img{height:200px}
.svc-label{height:66px;display:flex;align-items:center;justify-content:center;font-size:13px;font-weight:600;text-transform:uppercase;color:var(--ink);background:rgba(255,255,255,.88)}

/* remodel */
.remodel-title{left:73px;top:2876px;font-size:46px;line-height:50px;text-align:left}
.remodel-text{left:77px;top:3008px;width:400px;font-size:13px;line-height:22.5px;color:var(--ink)}
.ba{top:2894px;width:290px;height:380px}
.ba-label{position:absolute;left:30px;bottom:34px;font-family:"Poppins",sans-serif;font-weight:700;font-size:30px;color:var(--white)}

/* call band */
.call{left:0;top:3417px;width:1200px;height:631px;background:linear-gradient(180deg,#cfe7f3 0%,#4d8c5a 22%,#86cfe4 38%,#3fc6f2 55%,#5ed5f8 100%)}
.call-title{top:310px;width:100%;font-family:"Poppins",sans-serif;font-weight:700;font-size:78px;color:var(--white);text-shadow:0 4px 10px rgba(0,0,0,.35)}
.call-text{top:410px;left:170px;width:860px;font-size:13px;line-height:23px;color:var(--white)}

/* gallery */
.gallery-title{top:4160px;width:100%;font-size:46px}
.gallery-rule{left:564px;top:4234px;width:72px;height:3px;background:var(--aqua)}
.gal{position:absolute;border-radius:8px;overflow:hidden}
.dots{left:556px;top:4800px;display:flex;gap:8px}
.dots span{width:13px;height:13px;border-radius:50%;border:1.5px solid var(--aqua)}
.dots span.on{background:var(--aqua)}

/* footer */
.footer{left:0;top:4920px;width:1200px;height:370px;background:var(--aqua);color:var(--white)}
.foot-head{position:absolute;top:124px;font-size:13px;font-weight:600;text-transform:uppercase}
.foot-list{position:absolute;list-style:none;font-size:13px}
.foot-list li{display:flex;align-items:center;gap:8px;height:27px}
.contact-row{position:absolute;left:585px;display:flex;gap:14px;font-size:12.5px;line-height:15px}
.contact-ico{width:30px;height:30px;border:1.5px solid var(--white);display:flex;align-items:center;justify-content:center;flex:none}
.social{position:absolute;top:264px;left:137px;display:flex;gap:6px}
.social span{width:30px;height:30px;border:1.5px solid var(--white);border-radius:3px}
.copy{left:0;top:5290px;width:1200px;height:58px;background:var(--bar);color:var(--white);font-size:12px;display:flex;align-items:center;justify-content:center}
</style>
</head>
<body>

<header class="site-header">
  <div class="brand" style="left:77px;top:44px">
    <span class="brand-dot"></span>
    <span>Marlow<br>Pool Service</span>
  </div>
  <nav class="nav">
    <a class="active" style="left:388px">Home</a>
    <a style="left:459px">About Us</a>
    <a style="left:556px">Services</a>
    <a style="left:650px">Locations</a>
    <a style="left:756px">Gallery</a>
    <a style="left:843px">Contact Us</a>
  </nav>
  <div class="pill pill-solid" style="left:965px;top:56px;width:158px;height:39px;font-size:11.5px">Request a Quote</div>
</header>

<section class="abs hero" role="img" aria-label="Photo of a sparkling blue swimming pool with wooden deck and water jet">
  <div class="hero-shade"></div>
  <p class="abs center hero-kicker">WELCOME TO</p>
  <h1 class="abs center hero-title">MARLOW POOL SERVICES</h1>
  <p class="abs center hero-text">Lorem ipsum dolor sit amet, consectetuer adipiscing elit.<br>Aenean commodo ligula eget dolor.</p>
  <div class="pill pill-line" style="left:484px;top:405px;width:232px;height:58px;font-size:15px">Request a Quote</div>
</section>

<section class="stats">
  <div class="stat" style="left:73px">
    <div class="stat-icon"><svg width="34" height="34" viewBox="0 0 34 34" fill="none" stroke="#fff" stroke-width="2"><path d="M11 4v20M23 4v20M11 10h12M11 16h12M4 28c3 0 3-2 6-2s3 2 6 2 3-2 6-2 3 2 6 2"/></svg></div>
    <div class="stat-num">2000</div><div class="stat-label">Pools We Currently<br>Service</div>
  </div>
  <div class="stat" style="left:342px">
    <div class="stat-icon"><svg width="34" height="34" viewBox="0 0 34 34" fill="none" stroke="#fff" stroke-width="2"><circle cx="17" cy="17" r="11"/><path d="M17 10v7l5 3"/></svg></div>
    <div class="stat-num">33</div><div class="stat-label">Years in Business</div>
  </div>
  <div class="stat" style="left:612px">
    <div class="stat-icon"><svg width="34" height="34" viewBox="0 0 34 34"><path d="M17 3c-6 0-10 4.5-10 10 0 7 10 18 10 18s10-11 10-18c0-5.5-4-10-10-10z" fill="#fff"/><circle cx="17" cy="13" r="4" fill="#5fd4f7"/></svg></div>
    <div class="stat-num">23</div><div class="stat-label">Locations<br>Nationwide</div>
  </div>
  <div class="stat" style="left:880px">
    <div class="stat-icon"><svg width="34" height="34" viewBox="0 0 34 34" fill="none" stroke="#fff" stroke-width="2"><path d="M10 5h14v7a7 7 0 0 1-14 0zM10 8H5c0 5 3 7 5 7M24 8h5c0 5-3 7-5 7M17 19v6M11 30h12M13 25h8"/></svg></div>
    <div class="stat-num" style="margin-top:58px">12</div><div class="stat-label">Industry Awards</div>
  </div>
</section>

<section>
  <div class="photo video" role="img" aria-label="Video still of a tiled pool with steel ladder and garden deck">
    <svg class="play" viewBox="0 0 96 96"><circle cx="48" cy="48" r="44" fill="rgba(0,0,0,.45)" stroke="#fff" stroke-width="4"/><path d="M38 30l30 18-30 18z" fill="#fff"/></svg>
  </div>
  <div class="intro-card"></div>
  <h2 class="abs center serif-title intro-title">POOL SERVICE &amp; CLEANING</h2>
  <p class="abs center intro-text">Lorem ipsum dolor sit amet, consectetuer adipiscing elit. Aenean commodo ligula eget dolor. Aenean massa. Cum sociis natoque penatibus et magnis dis parturient montes, nascetur rid iculus mus. Donec quam felis, ultricies nec, pellentesque eu,</p>
  <div class="pill pill-solid" style="left:475px;top:1783px;width:260px;height:65px;font-size:12px;text-transform:uppercase">Find a Service Location</div>
</section>

<section class="abs services">
  <h2 class="abs center serif-title services-title">OUR POOL SERVICES</h2>
  <p class="abs center services-text">Lorem ipsum dolor sit amet, consectetuer adipiscing elit. Aenean commodo ligula eget dolor. Aenean massa. Cum sociis natoque penatibus et magnis dis parturient montes, nascetur ridiculus mus. Donec quam felis, ultricies nec, pellentesque eu, pretium</p>
  <div class="svc" style="left:73px"><div class="svc-img" role="img" aria-label="Backyard pool with white fence" style="background:linear-gradient(180deg,#c9d6de,#6fa9d8 55%,#2f86cf)"></div><div class="svc-label">Swimming Pool Services</div></div>
  <div class="svc" style="left:338px"><div class="svc-img" role="img" aria-label="Blue tiled pool and spa from above" style="background:linear-gradient(160deg,#3a7a3a,#1c78c8 40%,#2b9fe0)"></div><div class="svc-label">Pool Cleaning Service</div></div>
  <div class="svc" style="left:604px"><div class="svc-img" role="img" aria-label="Curved resort pool with swimmer" style="background:linear-gradient(160deg,#cfe0e0,#6cc5c8 45%,#3aa9b8)"></div><div class="svc-label">Swimming Pool Repair</div></div>
  <div class="svc" style="left:870px"><div class="svc-img" role="img" aria-label="Indoor pool under a glass roof" style="background:linear-gradient(180deg,#e3e8ef,#4d95e3 45%,#1f6fd0)"></div><div class="svc-label">Repair &amp; Replacement</div></div>
  <div class="pill pill-line" style="left:469px;top:598px;width:260px;height:72px;font-size:15px">View All Services</div>
</section>

<section>
  <h2 class="abs serif-title remodel-title">POOL<br>REMODELLING</h2>
  <p class="abs remodel-text">Lorem ipsum dolor sit amet, consectetuer adipiscing elit. Aenean commodo ligula eget dolor. Aenean massa. Cum sociis natoque penatibus et magnis dis parturient montes, nascetur ridiculus mus. Donec quam felis, ultricies nec, pellentesque eu, pretium quis, sem. Nulla consequa massa quis enim. Donec pede justo, fringilla vel,</p>
  <div class="pill pill-solid" style="left:73px;top:3197px;width:209px;height:67px;font-size:14px">Request Service</div>
  <div class="photo ba" style="left:534px;background:linear-gradient(180deg,#5a6a78,#3f7fb0 50%,#2a6e9c)" role="img" aria-label="Pool before remodelling, worn grey finish"><span class="ba-label">BEFORE</span></div>
  <div class="photo ba" style="left:829px;background:linear-gradient(160deg,#b9c2b8,#86d4e4 45%,#5ec9e6)" role="img" aria-label="Pool after remodelling, bright clear water"><span class="ba-label">AFTER</span></div>
</section>

<section class="abs call" role="img" aria-label="Resort pool with palm trees and poolside pavilion">
  <h2 class="abs center call-title">CALL US TODAY</h2>
  <p class="abs center call-text">Lorem ipsum dolor sit amet, consectetuer adipiscing elit. Aenean commodo ligula eget dolor. Aenean massaLorem ipsum dolor sit amet, consectetuer adipiscing elit. Aenean commodo ligula eget dolor. Aenean massa</p>
  <div class="pill pill-line" style="left:492px;top:480px;width:214px;height:64px;font-size:14px">Request a Quote</div>
</section>

<section>
  <h2 class="abs center serif-title gallery-title">Gallery</h2>
  <div class="abs gallery-rule"></div>
  <div class="gal" style="left:77px;top:4283px;width:342px;height:453px;background:linear-gradient(180deg,#9ccfe8,#3f8a3e 45%,#4fd0d8 80%,#d9e2e0)" role="img" aria-label="Palm trees beside a turquoise pool"></div>
  <div class="gal" style="left:436px;top:4283px;width:340px;height:218px;background:linear-gradient(160deg,#3b8fd8,#2a77c6 60%,#d6d9dc)" role="img" aria-label="Pool with steel ladder"></div>
  <div class="gal" style="left:436px;top:4517px;width:340px;height:219px;background:linear-gradient(180deg,#d9d3bf,#8fbfa3 45%,#4cb7c4)" role="img" aria-label="Apartment complex pool"></div>
  <div class="gal" style="left:789px;top:4283px;width:340px;height:218px;background:linear-gradient(180deg,#e7ecef,#5b9ad8 50%,#1e63c4)" role="img" aria-label="Pool with white lounge chairs"></div>
  <div class="gal" style="left:789px;top:4517px;width:340px;height:219px;background:linear-gradient(180deg,#cfe0ea,#4b7f3e 40%,#1f79cf 75%,#2f97df)" role="img" aria-label="Pool surrounded by trees"></div>
  <div class="abs dots"><span></span><span class="on"></span><span></span><span></span><span></span></div>
</section>

<footer class="abs footer">
  <div class="brand" style="left:106px;top:98px;color:var(--white)">
    <span class="brand-dot" style="background:var(--white)"></span>
    <span>Marlow<br>Pool Service</span>
  </div>
  <div class="social"><span></span><span></span><span></span><span></span></div>

  <div class="foot-head" style="left:390px">Quick Links</div>
  <ul class="foot-list" style="left:390px;top:182px">
    <li><svg width="14" height="10" viewBox="0 0 14 10" fill="none" stroke="#fff" stroke-width="1.6"><path d="M2 2l4 3-4 3M8 2l4 3-4 3"/></svg>Home</li>
    <li><svg width="14" height="10" viewBox="0 0 14 10" fill="none" stroke="#fff" stroke-width="1.6"><path d="M2 2l4 3-4 3M8 2l4 3-4 3"/></svg>About Us</li>
    <li><svg width="14" height="10" viewBox="0 0 14 10" fill="none" stroke="#fff" stroke-width="1.6"><path d="M2 2l4 3-4 3M8 2l4 3-4 3"/></svg>Services</li>
    <li><svg width="14" height="10" viewBox="0 0 14 10" fill="none" stroke="#fff" stroke-width="1.6"><path d="M2 2l4 3-4 3M8 2l4 3-4 3"/></svg>Contact Us</li>
    <li><svg width="14" height="10" viewBox="0 0 14 10" fill="none" stroke="#fff" stroke-width="1.6"><path d="M2 2l4 3-4 3M8 2l4 3-4 3"/></svg>Gallery</li>
  </ul>

  <div class="foot-head" style="left:585px">Contact Us</div>
  <div class="contact-row" style="top:190px">
    <span class="contact-ico"><svg width="14" height="14" viewBox="0 0 14 14"><path d="M3 1l3 3-1.5 2a8 8 0 0 0 3.5 3.5L10 8l3 3-2 2C6 13 1 8 1 3z" fill="#fff"/></svg></span>
    <span>CALL US<br>800 345 6789</span>
  </div>
  <div class="contact-row" style="top:240px">
    <span class="contact-ico"><svg width="14" height="12" viewBox="0 0 14 12" fill="none" stroke="#fff" stroke-width="1.4"><rect x="1" y="1" width="12" height="10"/><path d="M1 1l6 5 6-5"/></svg></span>
    <span>EMAIL US<br>info@websitename.com</span>
  </div>
  <div class="contact-row" style="top:290px">
    <span class="contact-ico"><svg width="12" height="14" viewBox="0 0 12 14"><path d="M6 0C3 0 1 2 1 5c0 4 5 9 5 9s5-5 5-9c0-3-2-5-5-5z" fill="#fff"/><circle cx="6" cy="5" r="2" fill="#5fd4f7"/></svg></span>
    <span>Address line Dummy Here<br>Address line Here</span>
  </div>

  <div class="foot-head" style="left:880px">Our Newsletter</div>
  <p class="abs" style="left:880px;top:186px;font-size:12.5px;line-height:17px">Subscribe our newsletter<br>to get the latest news</p>
  <div class="abs" style="left:880px;top:239px;width:188px;height:33px;background:var(--white)"></div>
  <div class="abs" style="left:880px;top:284px;width:109px;height:29px;background:var(--aqua-deep);font-size:10px;font-weight:600;display:flex;align-items:center;justify-content:center">SUBSCRIBE</div>
</footer>

<div class="abs copy">Copyright © 2024 All Rights Reserved By Company name</div>

</body>
</html>
```